KAJU Freightways #ALLKAJU Business Cards & Letterhead

I am looking to business cards designed for our organization. We are currently undergoing a small re-branding that is taking place. Our organization is called KAJU Freightways and we are headquartered in Phoenix, AZ. We primarily provide transportation and logistics services to the Marlow Parcel Bureau who is our largest customer. I would like to see a design that incorporates name, title, contact info, website, and address (this will be different depending on the employee). I would also like to see some color on the business card using our logo colors or a variation. I would like our logo on the back of the business card with the website displayed. The final design should communicate that we are a next generation transportation operate that focuses on being driver-first, customer-centric, innovative, and sustainable.We would also like our #ALLKAJU catch phrase incorporated as well.

Target Market(s)

Transportation & Logistics

Industry/Entity Type

Trucking Company

Contact Information for Business Card

-First and Last Name
-Position Title
-Contact Phone
-Contact Email
-Physical Address

Font styles to use
Serif

Colors

Designer to choose colors to be used in the design.

Requirements
Must have
• -KAJU logo prominently displayed
• -#ALLKAJU catch phrase used
• -Some amount of color, design gradient, etc.
• -Logo on the back with website listed (https://www.kajufreightco.example)

```html
<!DOCTYPE html>
<html lang="en">
<head>
<meta charset="utf-8">
<title>KAJU Freightways Business Card</title>
<link rel="stylesheet" href="https://fonts.googleapis.com/css2?family=Montserrat:wght@400;500;800&family=PT+Sans+Narrow:wght@400;700&display=swap">
<style>
  :root {
    --bg: #8a8a8a;
    --card: #ffffff;
    --navy: #063b48;
    --green: #7dc142;
    --map-grey: #d9d9d9;
    --text-grey: #555555;
  }
  * { box-sizing: border-box; margin: 0; padding: 0; }
  html, body { width: 1200px; height: 675px; overflow: hidden; }
  body {
    background: var(--bg);
    font-family: "Montserrat", sans-serif;
    position: relative;
  }
  .card {
    position: absolute;
    top: 187px;
    width: 525px;
    height: 300px;
    background: var(--card);
    border-radius: 16px;
    overflow: hidden;
    box-shadow: 0 6px 14px rgba(0,0,0,0.3);
  }
  .card--back { left: 50px; }
  .card--front { left: 625px; }

  /* back */
  .coverage-map {
    position: absolute;
    left: 60px; top: 28px;
    width: 405px; height: 200px;
    border-radius: 30px 40px 60px 30px;
    background: linear-gradient(100deg, var(--map-grey) 0%, var(--map-grey) 32%, var(--green) 48%, var(--green) 100%);
  }
  .map-badge {
    position: absolute;
    left: 85px; top: 55px;
    width: 90px; height: 90px;
    border-radius: 50%;
    background: var(--card);
    border: 4px solid var(--green);
    display: flex; align-items: center; justify-content: center;
  }
  .wordmark {
    font-family: "Montserrat", sans-serif;
    font-weight: 800;
    color: var(--navy);
    letter-spacing: 1px;
  }
  .map-badge .wordmark { font-size: 24px; }
  .back-url {
    position: absolute;
    right: 60px; bottom: 36px;
    font-size: 14px;
    color: var(--text-grey);
  }
  .back-url strong { color: var(--navy); font-weight: 800; }

  /* front */
  .brand {
    position: absolute;
    left: 40px; top: 70px;
    width: 210px;
    text-align: center;
  }
  .brand-badge {
    width: 120px; height: 120px;
    margin: 0 auto;
    border-radius: 50%;
    border: 5px solid var(--green);
    display: flex; align-items: center; justify-content: center;
  }
  .brand-badge .wordmark { font-size: 32px; }
  .brand-tagline {
    margin-top: 10px;
    font-family: "PT Sans Narrow", sans-serif;
    font-weight: 700;
    font-size: 17px;
    color: var(--green);
    white-space: nowrap;
  }
  .divider {
    position: absolute;
    left: 268px; top: 40px;
    width: 2px; height: 150px;
    background: linear-gradient(to bottom, rgba(0,0,0,0), rgba(0,0,0,0.35), rgba(0,0,0,0));
  }
  .contact {
    position: absolute;
    left: 290px; top: 44px;
    color: var(--text-grey);
    font-size: 11px;
    line-height: 1.45;
  }
  .contact-name {
    font-weight: 800;
    font-size: 17px;
    color: var(--navy);
    line-height: 1.1;
  }
  .contact-title {
    color: var(--green);
    font-size: 12px;
    font-weight: 500;
    margin-bottom: 8px;
  }
  .contact-address { margin-bottom: 10px; }
  .contact-list { list-style: none; }
  .contact-list li { display: flex; align-items: center; gap: 6px; }
  .contact-list svg { width: 11px; height: 11px; flex: none; }
  .accent-band {
    position: absolute;
    left: 0; bottom: 0;
    width: 100%; height: 70px;
  }
  .hashtag {
    position: absolute;
    right: 22px; bottom: 38px;
    font-weight: 800;
    font-size: 14px;
    color: var(--green);
  }
</style>
</head>
<body>

  <section class="card card--back">
    <div class="coverage-map" role="img" aria-label="Map of the United States showing service coverage states in green"></div>
    <div class="map-badge" style="left:145px; top:55px;">
      <span class="wordmark">KAJU</span>
    </div>
    <p class="back-url">www.<strong>kajufreightco</strong>.example</p>
  </section>

  <section class="card card--front">
    <div class="brand">
      <div class="brand-badge"><span class="wordmark">KAJU</span></div>
      <p class="brand-tagline">Transportation and Logistics Services</p>
    </div>

    <div class="divider"></div>

    <div class="contact">
      <p class="contact-name">RAE TALBOT</p>
      <p class="contact-title">President</p>
      <p class="contact-address">1460 North Saguaro Ridge Road<br>Glendale, AZ 85308</p>
      <ul class="contact-list">
        <li>
          <svg viewBox="0 0 12 12"><path d="M2.5 1 L4.5 1 L5 3.5 L3.8 4.5 Q5 7 7.5 8.2 L8.5 7 L11 7.5 L11 9.5 Q11 11 9.5 11 Q1 10 1 2.5 Q1 1 2.5 1Z" fill="#7dc142"/></svg>
          623-555-0142
        </li>
        <li>
          <svg viewBox="0 0 12 12"><rect x="0.5" y="2" width="11" height="8" fill="#7dc142"/><path d="M0.5 2 L6 6.5 L11.5 2" stroke="#fff" fill="none"/></svg>
          info@kajufreightco.example
        </li>
        <li>
          <svg viewBox="0 0 12 12"><circle cx="6" cy="6" r="5" fill="none" stroke="#7dc142" stroke-width="1.2"/><ellipse cx="6" cy="6" rx="2.2" ry="5" fill="none" stroke="#7dc142"/><line x1="1" y1="6" x2="11" y2="6" stroke="#7dc142"/></svg>
          www.kajufreightco.example
        </li>
      </ul>
    </div>

    <svg class="accent-band" viewBox="0 0 525 70" preserveAspectRatio="none" aria-hidden="true">
      <polygon points="0,62 390,40 525,40 525,70 0,70" fill="#7dc142"/>
      <polygon points="0,66 386,46 390,40 525,40 525,70 0,70" fill="#ffffff" opacity="0"/>
      <polygon points="395,0 525,0 525,70 385,70" fill="#063b48"/>
    </svg>
    <p class="hashtag">#ALLKAJU</p>
  </section>

</body>
</html>
```